Brightline Energy Product Distribution Brochure

We are looking to have our current brochure for our customers completely redesigned...the idea is to present the relevant information in an attractive way . Our website is brightlineenergyco.example where you can find more information about us. We have included a file with a rough idea of the page order and what each should include but feel free to adapt based on design. The example provided is only for context and doesnt have to be maintained. We will be using the brochure both digitally and in print form. As long as it reads easily and is eye catching, the design can be horizontal or vertical.Final deliverable should be indesign file.

"Our Brands" page: should be limited to one page (space being enough) where it has the header for each one (for example diesel generators) space for one or two lines of text and then the corresponding logos for each of the five categories
Updates

For those asking: the "our brands" page should be a single page layout where there is a header with the corresponding section and space for maybe one line of text followed by the two logos for that category. Each of the product pages should be similar in fashion to the one in the document attached: a photo of the product with some white space and space for the text to be included. We will be posting additional examples today

Target Market(s)

We want to present it to customers both digitally and in print so they can see our products

Industry/Entity Type

Power Generation

Font styles to use
Serif

Requirements
Must have
• Eye catching and able to present the information in a presentable fashion. Rest is up to you.
Nice to have
• Should incorporate the colors of our logo but can also add other depending on design

```html
<!DOCTYPE html>
<html lang="en">
<head>
<meta charset="utf-8">
<title>Brightline Energy – Distributor Program Guide</title>
<link href="https://fonts.googleapis.com/css2?family=Montserrat:wght@300;400;600;700;800&family=Open+Sans:wght@400;600&display=swap" rel="stylesheet">
<style>
  :root{
    --canvas:#d9d9d9;
    --paper:#f2f2f2;
    --paper-shade:#d4d4d4;
    --ink:#2b2b2b;
    --ink-soft:#555555;
    --charcoal:#2f2e30;
    --gold:#f2b51c;
    --gold-deep:#d99a0b;
    --photo-dark:#3a3a3c;
    --photo-light:#bdbdbd;
  }
  *{box-sizing:border-box;margin:0;padding:0}
  html,body{width:1200px;height:900px;overflow:hidden;background:var(--canvas)}
  body{font-family:'Montserrat',sans-serif;color:var(--ink);position:relative}

  .spread{position:absolute;left:100px;width:1000px;height:390px;display:flex;box-shadow:0 6px 18px rgba(0,0,0,.18)}
  .spread--covers{top:45px}
  .spread--products{top:470px}
  .page{position:relative;width:500px;height:390px;overflow:hidden;background:linear-gradient(160deg,#f7f7f7 0%,var(--paper) 45%,var(--paper-shade) 100%)}

  /* back cover */
  .back-band{position:absolute;left:0;right:0;top:225px;height:110px;background:var(--charcoal)}
  .back-frame{position:absolute;left:60px;top:40px;width:380px;height:290px;border:2px solid var(--gold)}
  .brand{display:flex;align-items:center;gap:10px;font-weight:600;color:var(--ink-soft);letter-spacing:.02em}
  .brand__mark{width:22px;height:22px;background:var(--gold)}
  .back-brand{position:absolute;left:0;right:0;top:120px;justify-content:center;font-size:22px}
  .contact{position:absolute;left:0;right:0;top:240px;text-align:center;color:var(--gold)}
  .contact__title{font-weight:600;font-size:15px;margin-bottom:14px}
  .contact__line{font-size:11px;line-height:20px;font-weight:400}

  /* front cover */
  .cover-art{position:absolute;inset:0}
  .cover-title{position:absolute;left:205px;top:175px;color:var(--gold);font-weight:800;font-size:27px;line-height:30px;letter-spacing:.02em}
  .cover-sub{position:absolute;left:205px;top:273px;color:#e6e6e6;font-size:10px;font-weight:400}
  .cover-brand{position:absolute;left:28px;top:270px;font-size:15px;color:#e8e8e8}
  .cover-brand .brand__mark{width:18px;height:18px}
  .perks{position:absolute;left:28px;bottom:10px;display:flex;gap:26px}
  .perk{display:flex;flex-direction:column;align-items:center;gap:4px;font-size:7px;font-weight:600;color:var(--ink-soft);text-transform:uppercase;text-align:center;line-height:9px;width:50px}
  .perk svg{width:22px;height:22px;stroke:var(--ink-soft);fill:none;stroke-width:1.4}

  /* product pages */
  .product-photo{position:absolute;border-radius:4px}
  .product-photo--regulator{left:22px;top:35px;width:215px;height:270px;background:linear-gradient(150deg,var(--photo-dark),#1f1f21 60%,#4a5a80)}
  .product-photo--controller{left:28px;top:90px;width:238px;height:180px;border-radius:12px;background:linear-gradient(180deg,#2e2e30,#1d1d1f)}
  .product-copy{position:absolute}
  .page--left .product-copy{left:285px;top:62px;width:200px}
  .page--right .product-copy{left:282px;top:62px;width:200px}
  .product-title{font-size:27px;line-height:34px;color:var(--ink-soft)}
  .product-title strong{font-weight:700;display:block}
  .product-title span{font-weight:400;display:block}
  .features-label{font-size:15px;font-weight:400;color:var(--ink);margin:22px 0 14px}
  .page--right .features-label{margin-top:28px}
  .feature-list{list-style:none;font-family:'Open Sans',sans-serif;font-size:6.3px;line-height:11px;font-weight:600;color:var(--ink)}
  .feature-list li{position:relative;padding-left:9px;margin-bottom:8px}
  .feature-list li::before{content:"✔";position:absolute;left:0;top:0;font-size:7px}
  .folio{position:absolute;bottom:10px;font-size:13px;color:var(--ink)}
  .page--left .folio{left:10px}
  .page--right .folio{right:14px}
  .accent-bar{position:absolute;bottom:6px;height:21px;width:295px}
  .accent-bar--dark{right:0;background:var(--charcoal)}
  .accent-bar--gold{left:0;background:var(--gold)}
</style>
</head>
<body>

<section class="spread spread--covers">
  <article class="page page--back-cover">
    <div class="back-band"></div>
    <div class="back-frame"></div>
    <div class="brand back-brand"><span class="brand__mark"></span>Brightline Energy</div>
    <div class="contact">
      <p class="contact__title">Contact Us</p>
      <p class="contact__line">4120 Harbor Line Ave, Coral Bay, FL 33000</p>
      <p class="contact__line">(555) 014-2290</p>
    </div>
  </article>

  <article class="page page--front-cover">
    <svg class="cover-art" viewBox="0 0 500 390" preserveAspectRatio="none">
      <defs>
        <linearGradient id="goldSweep" x1="0" y1="0" x2="1" y2="1">
          <stop offset="0" stop-color="#fbe08a"/>
          <stop offset=".5" stop-color="#f2b51c"/>
          <stop offset="1" stop-color="#d99a0b"/>
        </linearGradient>
        <linearGradient id="genTone" x1="0" y1="0" x2="0" y2="1">
          <stop offset="0" stop-color="#e9e9e9"/>
          <stop offset="1" stop-color="#9a9a9a"/>
        </linearGradient>
      </defs>
      <path d="M0 0 H90 Q30 40 0 120 Z" fill="url(#goldSweep)"/>
      <path d="M0 130 Q40 50 120 0 H140 Q60 50 20 140 Z" fill="#3a3a3c" opacity=".6"/>
      <rect role="img" aria-label="Photo of a trailer-mounted diesel generator" x="170" y="20" width="310" height="160" rx="4" fill="url(#genTone)"/>
      <path d="M0 230 L500 150 V300 Q420 330 330 345 L0 345 Z" fill="var(--charcoal)"/>
      <path d="M500 220 V345 H360 Q440 320 500 220 Z" fill="url(#goldSweep)"/>
      <rect x="0" y="345" width="500" height="45" fill="#f4f4f4"/>
    </svg>
    <div class="brand cover-brand"><span class="brand__mark"></span>Brightline Energy</div>
    <h1 class="cover-title">DISTRIBUTOR<br>PROGRAM<br>GUIDE</h1>
    <p class="cover-sub">Diesel Generators | Alternators | Parts</p>
    <div class="perks">
      <div class="perk"><svg viewBox="0 0 24 24"><circle cx="12" cy="7" r="4"/><path d="M4 21c1-5 4-7 8-7s7 2 8 7"/></svg>Team of experts</div>
      <div class="perk"><svg viewBox="0 0 24 24"><circle cx="12" cy="12" r="9"/><path d="M12 7v5l3 3"/></svg>Same day urgency</div>
      <div class="perk"><svg viewBox="0 0 24 24"><circle cx="12" cy="12" r="4"/><path d="M12 2v4M12 18v4M2 12h4M18 12h4M5 5l3 3M16 16l3 3M19 5l-3 3M8 16l-3 3"/></svg>100% original</div>
    </div>
  </article>
</section>

<section class="spread spread--products">
  <article class="page page--left">
    <div class="product-photo product-photo--regulator" role="img" aria-label="Photo of an alternator voltage regulator board"></div>
    <div class="product-copy">
      <h2 class="product-title"><strong>Alternator</strong><span>Parts</span></h2>
      <p class="features-label">FEATURES</p>
      <ul class="feature-list">
        <li>Lorem ipsum dolor sit amet, consectetur<br>adipiscing elit, sed do eiusmod tempor incididunt</li>
        <li>Lorem ipsum dolor sit amet, consectetur<br>adipiscing elit, sed do eiusmod tempor incididunt</li>
        <li>Lorem ipsum dolor sit amet, consectetur<br>adipiscing elit, sed do eiusmod tempor incididunt</li>
        <li>Lorem ipsum dolor sit amet, consectetur<br>adipiscing elit, sed do eiusmod tempor incididunt</li>
      </ul>
    </div>
    <span class="folio">10</span>
    <div class="accent-bar accent-bar--dark"></div>
  </article>

  <article class="page page--right">
    <div class="product-photo product-photo--controller" role="img" aria-label="Photo of a generator control module with display and buttons"></div>
    <div class="product-copy">
      <h2 class="product-title"><strong>Controllers</strong></h2>
      <p class="features-label">FEATURES</p>
      <ul class="feature-list">
        <li>Lorem ipsum dolor sit amet, consectetur<br>adipiscing elit, sed do eiusmod tempor incididunt</li>
        <li>Lorem ipsum dolor sit amet, consectetur<br>adipiscing elit, sed do eiusmod tempor incididunt</li>
        <li>Lorem ipsum dolor sit amet, consectetur<br>adipiscing elit, sed do eiusmod tempor incididunt</li>
        <li>Lorem ipsum dolor sit amet, consectetur<br>adipiscing elit, sed do eiusmod tempor incididunt</li>
      </ul>
    </div>
    <span class="folio">11</span>
    <div class="accent-bar accent-bar--gold"></div>
  </article>
</section>

</body>
</html>
```